Design 4 pages for an event discovery website

This is a contest for the design of 4 pages for an events discovery website. The feature is part of the new sign-up process.

Please see the attached document for a full scope, mockups and the parent category icons.

Target Market(s)

18-35 Australian event goers

Industry/Entity Type

Events

Number of Pages Required

4 page

```html
<!DOCTYPE html>
<html lang="en">
<head>
<meta charset="utf-8">
<title>eventyra – Sign Up</title>
<link rel="stylesheet" href="https://fonts.googleapis.com/css2?family=Open+Sans:ital,wght@0,400;0,600;0,700;1,700&display=swap">
<style>
  :root {
    --ink: #000000;
    --white: #ffffff;
    --rule: #5a5a5a;
    --field: #ffffff;
    --field-text: #9a9a9a;
    --social: #2f5d9c;
    --social-divider: #264d83;
    --cta-top: #e27a3a;
    --cta-bottom: #c85a1e;
    --cta-border: #8e3f14;
    --panel-frame: rgba(90, 90, 90, 0.55);
    --panel: #000000;
    --bullet: #2aa4e4;
    --bokeh-1: #7a0a2a;
    --bokeh-2: #3a0616;
  }
  * { box-sizing: border-box; margin: 0; padding: 0; }
  html, body { width: 1200px; height: 698px; overflow: hidden; background: var(--ink); }
  body { font-family: "Open Sans", Arial, sans-serif; color: var(--white); position: relative; }

  .site-header {
    position: absolute; left: 0; top: 0; width: 1200px; height: 98px;
    background: var(--ink); border-bottom: 1px solid var(--rule);
  }
  .brand {
    position: absolute; left: 38px; top: 22px;
    font-size: 44px; font-weight: 700; letter-spacing: -1px; color: var(--white); line-height: 1;
  }
  .nav-find {
    position: absolute; left: 302px; top: 37px;
    font-size: 13px; font-weight: 600; color: var(--white);
  }
  .search {
    position: absolute; left: 786px; top: 30px; width: 204px; height: 38px;
    background: var(--field); border-radius: 3px;
  }
  .search span { position: absolute; left: 11px; top: 9px; font-size: 15px; color: var(--field-text); }
  .search svg { position: absolute; right: 12px; top: 10px; }
  .account-links {
    position: absolute; left: 1019px; top: 38px; font-size: 15px; color: var(--white);
  }
  .account-links .sep { margin: 0 10px; }

  .stage {
    position: absolute; left: 0; top: 99px; width: 1200px; height: 541px;
    background:
      radial-gradient(circle at 15% 30%, var(--bokeh-1) 0, transparent 22%),
      radial-gradient(circle at 78% 85%, var(--bokeh-1) 0, transparent 25%),
      radial-gradient(circle at 45% 10%, var(--bokeh-2) 0, transparent 20%),
      radial-gradient(circle at 92% 30%, var(--bokeh-1) 0, transparent 18%),
      radial-gradient(circle at 30% 90%, var(--bokeh-2) 0, transparent 25%),
      var(--ink);
  }

  .signup-title {
    position: absolute; left: 74px; top: 240px;
    display: flex; align-items: center; gap: 8px;
    font-size: 29px; font-weight: 600;
  }
  .social-button {
    position: absolute; left: 103px; top: 294px; width: 251px; height: 132px;
    background: var(--social); display: flex;
  }
  .social-button .mark-slot { width: 70px; border-right: 2px solid var(--social-divider); }
  .social-button .label {
    padding: 18px 0 0 18px; font-size: 20px; line-height: 36px; color: var(--white);
  }
  .email-button {
    position: absolute; left: 68px; top: 485px; width: 318px; height: 53px;
    background: linear-gradient(var(--cta-top), var(--cta-bottom));
    border: 1px solid var(--cta-border); border-radius: 3px;
    font-size: 16.5px; color: var(--white);
    display: flex; align-items: center; justify-content: center;
  }

  .benefits-frame {
    position: absolute; left: 451px; top: 162px; width: 708px; height: 394px;
    background: var(--panel-frame); border-radius: 3px;
  }
  .benefits {
    position: absolute; left: 12px; top: 12px; right: 12px; bottom: 12px;
    background: var(--panel); border-radius: 3px; list-style: none;
    padding-top: 24px;
  }
  .benefits li {
    display: flex; align-items: center; height: 57.6px; padding-left: 27px;
    font-size: 16.6px; font-weight: 700; font-style: italic;
  }
  .benefits li svg { flex: none; margin-right: 19px; }

  .site-footer {
    position: absolute; left: 0; top: 640px; width: 1200px; height: 58px;
    background: var(--ink); border-top: 1px solid var(--rule);
    display: flex; align-items: center; justify-content: center;
    font-size: 15.5px;
  }
</style>
</head>
<body>
  <header class="site-header">
    <div class="brand">eventyra</div>
    <div class="nav-find">FIND EVENT</div>
    <div class="search">
      <span>search</span>
      <svg width="18" height="18" viewBox="0 0 18 18"><circle cx="7" cy="7" r="5.5" fill="none" stroke="#bbb" stroke-width="2"/><line x1="11" y1="11" x2="16" y2="16" stroke="#bbb" stroke-width="2.5"/></svg>
    </div>
    <div class="account-links">SIGN UP<span class="sep">|</span>LOGIN</div>
  </header>

  <main class="stage" role="img" aria-label="Dark background with soft crimson bokeh lights and sparkles"></main>

  <h1 class="signup-title">
    <svg width="34" height="28" viewBox="0 0 34 28"><path d="M4 26 C4 14 12 9 24 9" fill="none" stroke="#fff" stroke-width="4" stroke-linecap="round"/><path d="M20 2 L31 9 L20 16 Z" fill="#fff"/></svg>
    Sign Up
  </h1>
  <div class="social-button">
    <div class="mark-slot"></div>
    <div class="label">Connect<br>with<br>Circlebook</div>
  </div>
  <div class="email-button">Click here to sign up without Circlebook</div>

  <section class="benefits-frame">
    <ul class="benefits">
      <li><svg width="24" height="24" viewBox="0 0 24 24"><circle cx="12" cy="12" r="11" fill="var(--bullet)"/><path d="M10 8 L14 12 L10 16" fill="none" stroke="#fff" stroke-width="2"/></svg>Get personalised event recommendations</li>
      <li><svg width="24" height="24" viewBox="0 0 24 24"><circle cx="12" cy="12" r="11" fill="var(--bullet)"/><path d="M10 8 L14 12 L10 16" fill="none" stroke="#fff" stroke-width="2"/></svg>Get notified about your favourite events - never miss out again</li>
      <li><svg width="24" height="24" viewBox="0 0 24 24"><circle cx="12" cy="12" r="11" fill="var(--bullet)"/><path d="M10 8 L14 12 L10 16" fill="none" stroke="#fff" stroke-width="2"/></svg>Follow all your favourite artists, musicians, teams and players in one place</li>
      <li><svg width="24" height="24" viewBox="0 0 24 24"><circle cx="12" cy="12" r="11" fill="var(--bullet)"/><path d="M10 8 L14 12 L10 16" fill="none" stroke="#fff" stroke-width="2"/></svg>Follow your favourite local venues to know everything happening there</li>
      <li><svg width="24" height="24" viewBox="0 0 24 24"><circle cx="12" cy="12" r="11" fill="var(--bullet)"/><path d="M10 8 L14 12 L10 16" fill="none" stroke="#fff" stroke-width="2"/></svg>Get curated news and feature content on your favourite artists (coming soon)</li>
      <li><svg width="24" height="24" viewBox="0 0 24 24"><circle cx="12" cy="12" r="11" fill="var(--bullet)"/><path d="M10 8 L14 12 L10 16" fill="none" stroke="#fff" stroke-width="2"/></svg>Invite your mates to events via Circlebook (CB sign-up only</li>
    </ul>
  </section>

  <footer class="site-footer">© 2015 eventyra. All Rights Reserved.</footer>
</body>
</html>
```